Events publishing website

Have increased the budget for Coded website design. Thanks
-
We need a wordpress website for events publishing. The website will be using all different kinds of events (social, business, music etc). The website should allow user to submit the new events. the new events will be published after admin reviewed.
Key menu items & requirements
- New Events (1-show picture, short description & start/end date. User can view more details in another page. 2-have categories, such as locations, free/ticked, event type etc. 3 - allow user to share the events in social website)
- Event organizer list (show the full list and most popular event organizers. users can view the list by categories, similar to above)
- events establishments (allow user to publish events related informations such as equipments, venue informations etc)
- discussion forum
Key functions
-registration page (new users should fill name, location, normal users or event organizer, types of event organizer etc)
-allow user to change locations to view different events
-search function
The functions should be similar to the following, the design should not. The website should not look like a proper website.
http://www.plavorgatherings.example
Reason: Hi All, have extended few days to allow some changes to be made for current design. Thanks

```html
<!DOCTYPE html>
<html lang="en">
<head>
<meta charset="utf-8">
<title>Events – Registration</title>
<link href="https://fonts.googleapis.com/css2?family=Ropa+Sans&family=Roboto:wght@400&family=Open+Sans:wght@400&display=swap" rel="stylesheet">
<style>
  :root{
    --teal:#3f7c75;
    --teal-dark:#2f625c;
    --teal-light:#5a958d;
    --ink:#222;
    --beige:#f3f1ea;
    --beige-edge:#e4e1d8;
    --field-border:#d9dcd9;
    --orange:#f2a520;
    --white:#fff;
  }
  *{box-sizing:border-box;margin:0;padding:0}
  html,body{width:902px;height:1200px;overflow:hidden}
  body{
    position:relative;
    font-family:"Roboto",sans-serif;color:var(--ink);
    background:radial-gradient(ellipse at 50% 10%, var(--beige) 0%, var(--beige-edge) 100%);
  }
  .abs{position:absolute}

  .topbar{left:0;top:0;width:902px;height:26px;background:#141414;
    font-family:"Open Sans",sans-serif;font-size:9px;color:#fff;
    display:flex;align-items:center;padding-left:25px;gap:9px}
  .topbar .sep{color:#aaa}

  .brand{left:33px;top:55px}
  .brand-name{font-family:"Ropa Sans",sans-serif;font-weight:400;font-size:32px;color:var(--teal);line-height:1}
  .brand-slogan{font-family:"Ropa Sans",sans-serif;font-weight:400;font-size:14px;color:var(--teal);margin-top:2px}

  .account{top:42px;right:38px;display:flex;gap:14px;font-family:"Ropa Sans",sans-serif;font-weight:400;font-size:13px;color:var(--teal-dark)}
  .account span{display:flex;align-items:flex-end;gap:3px}

  .search{left:626px;top:82px;width:258px;height:30px;background:var(--white);border:1px solid var(--field-border);display:flex}
  .search-input{flex:1;font-family:"Ropa Sans",sans-serif;font-size:13px;color:#777;padding:6px 9px}
  .search-go{width:29px;background:var(--orange);color:#fff;font-family:"Ropa Sans",sans-serif;font-size:14px;display:flex;align-items:center;justify-content:center}

  .mainnav{left:26px;top:128px;width:861px;height:50px;background:linear-gradient(#4a8880,var(--teal-dark));
    display:flex;align-items:center;font-family:"Ropa Sans",sans-serif;font-weight:400;font-size:15px;color:#fff;border-bottom:2px solid #fff}
  .mainnav a{padding:0 21px;height:34px;display:flex;align-items:center;border-right:1px dotted rgba(255,255,255,.35);color:#fff;text-decoration:none}
  .mainnav a:first-child{padding-left:30px}
  .mainnav a:last-child{border-right:none}

  .banner{left:26px;top:180px;width:861px;height:266px;
    background:linear-gradient(90deg,#5b4a3a 0%,#7a6a55 25%,#3b2a22 48%,#b84a1a 62%,#e6a12a 72%,#a6361a 85%,#6a2a1a 100%)}
  .banner-arrow{top:283px;width:23px;height:36px;background:rgba(255,255,255,.9);color:#888;font-size:16px;display:flex;align-items:center;justify-content:center}
  .banner-arrow.prev{left:26px;border-radius:0 18px 18px 0}
  .banner-arrow.next{left:868px;border-radius:18px 0 0 18px}

  .panel{left:34px;top:453px;width:843px;height:466px;background:var(--white);border:1px solid #e3e3e3}
  .panel-title{left:62px;top:488px;font-family:"Ropa Sans",sans-serif;font-weight:400;font-size:15px}
  .panel-rule{left:61px;top:517px;width:157px;border-top:1px dotted #333}
  .field-label{width:240px;left:65px;text-align:right;font-size:13px;line-height:16px}
  .field-input{left:318px;width:225px;height:30px;border:1px solid var(--field-border);border-radius:3px;background:#fff}
  .radio{display:flex;align-items:center;gap:10px;font-family:"Ropa Sans",sans-serif;font-size:14px;color:#555}
  .radio i{width:18px;height:18px;border-radius:50%;border:1px solid #ddd;background:#f7f7f7;display:flex;align-items:center;justify-content:center}
  .radio i.on::after{content:"";width:6px;height:6px;border-radius:50%;background:#666}
  .submit{left:425px;top:835px;width:93px;height:31px;background:var(--teal);border-radius:3px;color:#fff;
    font-family:"Ropa Sans",sans-serif;font-weight:400;font-size:14px;display:flex;align-items:center;justify-content:center}
  .caret{left:737px;top:553px;font-size:10px;color:#333}

  .footer{left:26px;top:928px;width:862px;height:272px;background:linear-gradient(var(--teal-light),var(--teal-dark))}
  .footer-title{font-family:"Ropa Sans",sans-serif;font-weight:400;font-size:16px;color:#fff}
  .links{left:63px;top:975px;width:489px;font-family:"Open Sans",sans-serif;font-size:11px;color:#fff}
  .links-row{display:grid;grid-template-columns:97px 123px 123px 1fr;height:24.5px;align-items:center;border-bottom:1px dashed rgba(255,255,255,.35);padding-left:4px}
  .social{left:603px;top:975px;display:flex;gap:5px}
  .social i{width:23px;height:23px;border-radius:50%;background:#fff}
  .copyright{left:44px;top:1112px;width:826px;height:42px;background:rgba(0,0,0,.12);
    font-family:"Open Sans",sans-serif;font-size:9px;color:#fff;display:flex;align-items:center;padding-left:17px}
</style>
</head>
<body>
  <div class="abs topbar">
    <span>EVENTS</span><span class="sep">|</span><span>NEWS EVENTS</span><span class="sep">|</span><span>SAVOR</span><span class="sep">|</span><span>EVENT INTERNATIONAL ART SERIES</span><span class="sep">|</span><span>PLAVOR EVENTS CALENDAR</span>
  </div>

  <div class="abs brand">
    <div class="brand-name">Events</div>
    <div class="brand-slogan">your company slogan here</div>
  </div>

  <div class="abs account">
    <span><svg width="16" height="16" viewBox="0 0 16 16"><path d="M1 7h3v8H1zM5 7l4-6c1 0 2 1 1.5 3L10 6h4c1 0 1.5 1 1 2l-2 6c-.3.7-1 1-1.5 1H5z" fill="#2f625c"/></svg>SIGN UP</span>
    <span><svg width="14" height="18" viewBox="0 0 14 18"><path d="M3 8V5a4 4 0 018 0v3h-2V5a2 2 0 00-4 0v3z" fill="#2f625c"/><rect x="1" y="8" width="12" height="10" rx="1" fill="#2f625c"/></svg>LOGIN</span>
    <span><svg width="20" height="20" viewBox="0 0 20 20"><circle cx="10" cy="5" r="4" fill="#2f625c"/><path d="M1 20c0-6 4-9 9-9s9 3 9 9z" fill="#2f625c"/></svg>MEMBER</span>
  </div>

  <div class="abs search">
    <div class="search-input">Enter Keyword here</div>
    <div class="search-go">Go</div>
  </div>

  <nav class="abs mainnav">
    <a>MAIN</a><a>POPULAR</a><a>EVENT ORGANIZER</a><a>FORUM</a><a>HELP</a><a>CONTACT US</a>
  </nav>

  <div class="abs banner" role="img" aria-label="Conference hall with rows of chairs, projection screens and warm stage lighting"></div>
  <div class="abs banner-arrow prev">&#10094;</div>
  <div class="abs banner-arrow next">&#10095;</div>

  <div class="abs panel"></div>
  <div class="abs panel-title">Registration</div>
  <div class="abs panel-rule"></div>
  <div class="abs caret">&#8964;</div>

  <div class="abs field-label" style="top:553px">First Name :</div>
  <div class="abs field-input" style="top:546px"></div>
  <div class="abs field-label" style="top:598px">Last Name :</div>
  <div class="abs field-input" style="top:591px"></div>
  <div class="abs field-label" style="top:644px">Email :</div>
  <div class="abs field-input" style="top:637px"></div>
  <div class="abs field-label" style="top:692px">Event organizer :</div>
  <div class="abs radio" style="left:318px;top:691px"><i class="on"></i>Yes<i style="margin-left:16px"></i>No</div>
  <div class="abs field-label" style="top:735px">Location :</div>
  <div class="abs field-input" style="top:728px"></div>
  <div class="abs field-label" style="top:782px">Organizer types :</div>
  <div class="abs field-input" style="top:775px"></div>
  <div class="abs submit">SUBMIT</div>

  <footer class="abs footer"></footer>
  <div class="abs footer-title" style="left:63px;top:944px">Quick Links</div>
  <div class="abs footer-title" style="left:601px;top:944px">Connect with Us</div>
  <div class="abs links">
    <div class="links-row"><span>Hom page</span><span>Login</span><span>Support</span><span>Term &amp; Conditions of Use</span></div>
    <div class="links-row"><span>Events</span><span>FAQ</span><span>Add Events</span><span>Privacy Policy</span></div>
    <div class="links-row"><span>Popular</span><span>Login</span><span>Speical Events</span><span>Help</span></div>
    <div class="links-row"><span>News</span><span>Forgot Password</span><span>Contact info</span><span></span></div>
  </div>
  <div class="abs social"><i></i><i></i><i></i></div>
  <div class="abs copyright">© 2012 Company Name &nbsp;|&nbsp; All right reserved &nbsp;|&nbsp; Policy Privacy</div>
</body>
</html>
```